NZ First of it's kind solutions directory and marketplace for busy Mums needs a business card design

We need a business card design for our new nationwide business in NZ (long term plans to go global). We provide solutions to the everyday challenges that busy Mums face by connecting them with quality communities and suppliers of carefully selected, relevant products and services. We sell direct via our online marketplace. The final design should communicate our values of inclusivity, quality and smart solutions. Colours should incorporate our logo colour palette of #477077 and #6ba8b2. Our website is at https://www.brightnestmums.example

Target Market(s)

busy Mums, Age 28 – 50, female, income over $100K, location main centres NZ primarily but NZ wide. Is likely juggling work or career with a young family. Probably had hobbies which have fallen by the wayside.
-Wants to succeed in her chosen career without compromising on family life
-to successfully juggle her career without feeling like she is compromising her children
- Is time poor, something always has to give and it’s generally her health (she’ll stay up late, get stressed)
- probably ex corporate or professional career. Has discretional income

Industry/Entity Type

Business

Contact Information for Business Card

Lena Forbisher, Founder, BrightNestMums.example (Strapline Tap; Gather; Sorted), 47 Kowhai Terrace, Ellerslie, Auckland 1051, New Zealand. Mob: 021 483 517 Ph: +64 (0)9 571 4860

Font styles to use
Other font styles liked:
• Raleway, and/or Architects Daughter

Colors
00a990
33b8a4
86cfc6
cfeae6

Requirements
Must have
• the above details, streamline. the logo and colours associated with those logos
Should not have
• foil or metallic colours

```html
<!DOCTYPE html>
<html lang="en">
<head>
<meta charset="utf-8">
<title>BrightNest Mums – Business Card</title>
<link rel="stylesheet" href="https://fonts.googleapis.com/css2?family=Roboto:ital,wght@0,400;0,500;0,700;1,400&display=swap">
<style>
  :root {
    --teal-deep: #41626a;
    --teal-deeper: #3a5960;
    --teal-brand: #477077;
    --teal-light: #6ba8b2;
    --paper: #f6f7f7;
    --backdrop: #e8e9e9;
    --ink-white: #ffffff;
    --ink-soft: #e3ecee;
    --ink-grey: #5b6b6f;
  }
  html, body {
    margin: 0;
    padding: 0;
    width: 1200px;
    height: 576px;
    overflow: hidden;
    background: var(--backdrop);
    font-family: "Roboto", Arial, sans-serif;
  }
  .canvas {
    position: relative;
    width: 1200px;
    height: 576px;
  }
  .card {
    position: absolute;
    top: 138px;
    width: 484px;
    height: 292px;
    border-radius: 14px;
    overflow: hidden;
  }

  /* Front */
  .card-front {
    left: 82px;
    background: linear-gradient(160deg, var(--teal-deep), var(--teal-deeper));
  }
  .front-wordmark {
    position: absolute;
    left: 0;
    right: 0;
    top: 106px;
    text-align: center;
    color: var(--ink-white);
    font-weight: 700;
    font-size: 44px;
    letter-spacing: -0.5px;
    line-height: 1;
  }
  .front-strapline {
    position: absolute;
    left: 0;
    right: 0;
    top: 172px;
    text-align: center;
    color: var(--ink-soft);
    font-size: 14px;
    letter-spacing: 5px;
  }

  /* Back */
  .card-back {
    left: 602px;
    width: 481px;
    height: 290px;
    background: var(--teal-deep);
  }
  .back-panel {
    position: absolute;
    inset: 0;
  }
  .person-name {
    position: absolute;
    left: 25px;
    top: 18px;
    margin: 0;
    color: var(--ink-white);
    font-weight: 700;
    font-size: 19px;
  }
  .person-role {
    position: absolute;
    left: 25px;
    top: 47px;
    margin: 0;
    color: var(--ink-soft);
    font-style: italic;
    font-size: 11.5px;
  }
  .address {
    position: absolute;
    left: 25px;
    top: 157px;
    margin: 0;
    color: var(--ink-soft);
    font-style: normal;
    font-size: 12.5px;
    line-height: 18px;
  }
  .contact-list {
    position: absolute;
    left: 25px;
    top: 201px;
    margin: 0;
    padding: 0;
    list-style: none;
    color: var(--ink-soft);
    font-size: 12.5px;
    line-height: 18.4px;
  }
  .contact-list li {
    display: flex;
    align-items: center;
    gap: 7px;
  }
  .contact-icon {
    width: 11px;
    height: 11px;
    flex: none;
  }
  .brand-mark {
    position: absolute;
    left: 316px;
    top: 128px;
    width: 36px;
    height: 36px;
    border-radius: 50%;
    background: var(--teal-brand);
  }
  .back-wordmark {
    position: absolute;
    left: 410px;
    top: 146px;
    transform: translate(-50%, -50%) rotate(-90deg);
    white-space: nowrap;
    color: var(--teal-brand);
    font-weight: 700;
    font-size: 30px;
    letter-spacing: -0.5px;
  }
  .back-strapline {
    position: absolute;
    left: 437px;
    top: 146px;
    transform: translate(-50%, -50%) rotate(-90deg);
    white-space: nowrap;
    color: var(--ink-grey);
    font-size: 10px;
    letter-spacing: 3.5px;
  }
</style>
</head>
<body>
<main class="canvas">

  <section class="card card-front" aria-label="Card front">
    <div class="front-wordmark">BrightNest Mums</div>
    <div class="front-strapline">TAP | GATHER | SORTED</div>
  </section>

  <section class="card card-back" aria-label="Card back">
    <svg class="back-panel" viewBox="0 0 481 290" preserveAspectRatio="none" aria-hidden="true">
      <path d="M282 0 Q226 145 282 290 L481 290 L481 0 Z" fill="var(--teal-light)"/>
      <path d="M288 0 Q232 145 288 290 L481 290 L481 0 Z" fill="var(--paper)"/>
    </svg>

    <h1 class="person-name">Lena Forbisher</h1>
    <p class="person-role">Founder</p>

    <address class="address">
      47 Kowhai Terrace, Ellerslie,<br>
      Auckland 1051, New Zealand
    </address>

    <ul class="contact-list">
      <li>
        <svg class="contact-icon" viewBox="0 0 12 12" aria-hidden="true"><rect x="3" y="0.5" width="6" height="11" rx="1.2" fill="none" stroke="#e3ecee" stroke-width="1.2"/><circle cx="6" cy="9.5" r="0.8" fill="#e3ecee"/></svg>
        <span>021 483 517</span>
      </li>
      <li>
        <svg class="contact-icon" viewBox="0 0 12 12" aria-hidden="true"><path d="M1 4 Q6 0 11 4 L9.5 5.5 L8 4.5 L4 4.5 L2.5 5.5 Z" fill="#e3ecee"/><rect x="2.5" y="6" width="7" height="5" rx="1" fill="#e3ecee"/></svg>
        <span>+64 (0)9 571 4860</span>
      </li>
      <li>
        <svg class="contact-icon" viewBox="0 0 12 12" aria-hidden="true"><rect x="0.5" y="2.5" width="11" height="7" fill="#e3ecee"/><path d="M0.5 2.5 L6 7 L11.5 2.5" fill="none" stroke="#41626a" stroke-width="1"/></svg>
        <span>www.BrightNestMums.example</span>
      </li>
      <li>
        <svg class="contact-icon" viewBox="0 0 12 12" aria-hidden="true"><circle cx="6" cy="6" r="5" fill="none" stroke="#e3ecee" stroke-width="1.2"/><ellipse cx="6" cy="6" rx="2" ry="5" fill="none" stroke="#e3ecee" stroke-width="1"/><line x1="1" y1="6" x2="11" y2="6" stroke="#e3ecee" stroke-width="1"/></svg>
        <span>lena@brightnestmums.example</span>
      </li>
    </ul>

    <div class="brand-mark" aria-hidden="true"></div>
    <div class="back-wordmark">BrightNest Mums</div>
    <div class="back-strapline">TAP | GATHER | SORTED</div>
  </section>

</main>
</body>
</html>
```